Request for Business Card Design

Hi. My name is Marlene, I am looking for a new business card design for my company, Quarrow Signal Instruments, LLC. I really like the design you did for Tarsel Venture and was hoping you could do something similar using our full logo and our mark. I am also open to any raised texture design using our mark. I have attached our full logo, which would need to be somewhere on the card, as well as the mark in both outline and full form, as well as our brand colors / guide. The card does not have to be white, as long as our logo and mark appear. I actually like darker colored business cards more, but am open to all options. If you are interested in working with me, please let me know. We would also take the business card design into letterhead design if you can do that.

```html
<!DOCTYPE html>
<html lang="en">
<head>
<meta charset="utf-8">
<title>Quarrow Signal Instruments – Business Card</title>
<link rel="stylesheet" href="https://fonts.googleapis.com/css2?family=Open+Sans:wght@400;600;700;800&display=swap">
<style>
  :root {
    --stage: #222223;
    --card: #3c3c3e;
    --card-dark: #333335;
    --pattern-light: #5a5a5c;
    --accent: #1e94c4;
    --ink: #ffffff;
    --ghost: #45505a;
  }
  * { box-sizing: border-box; margin: 0; padding: 0; }
  html, body {
    width: 1200px; height: 780px; overflow: hidden;
    background: var(--stage);
    font-family: "Open Sans", Arial, sans-serif;
  }
  .canvas { position: relative; width: 1200px; height: 780px; }

  .card {
    position: absolute;
    width: 540px; height: 310px;
    background: var(--card);
    border-bottom: 6px solid var(--accent);
    overflow: hidden;
    box-shadow: 0 12px 30px rgba(0,0,0,.45);
  }

  /* Back of card */
  .card--back { left: 50px; top: 70px; background: var(--card-dark); }
  .card__texture {
    position: absolute; inset: 0;
    background: radial-gradient(ellipse at 100% 0%, var(--pattern-light) 0%, var(--card-dark) 60%);
  }
  .brand {
    position: absolute; right: 26px; bottom: 24px;
    display: flex; align-items: center; gap: 10px;
  }
  .brand__dot {
    width: 22px; height: 22px; border-radius: 50%;
    background: var(--accent);
  }
  .brand__name {
    color: var(--ink); font-weight: 700; font-size: 13px;
    letter-spacing: 1.5px; text-transform: uppercase;
  }

  /* Front of card */
  .card--front { left: 610px; top: 400px; }
  .card__glow {
    position: absolute; left: 200px; top: 40px;
    width: 300px; height: 240px; border-radius: 50%;
    background: radial-gradient(circle, rgba(69,80,90,.9) 0%, rgba(69,80,90,0) 70%);
  }
  .identity {
    position: absolute; left: 70px; top: 112px; text-align: right; width: 170px;
  }
  .identity__name {
    color: var(--accent); font-weight: 800; font-size: 40px; line-height: 1;
  }
  .identity__role {
    color: var(--ink); font-weight: 600; font-size: 16px; margin-top: 2px;
  }
  .divider {
    position: absolute; left: 258px; top: 92px;
    width: 2px; height: 96px; background: var(--ink);
  }
  .contacts {
    position: absolute; left: 276px; top: 96px;
    list-style: none;
  }
  .contacts__item {
    display: flex; align-items: center; gap: 8px;
    color: var(--ink); font-size: 13px; line-height: 22px;
  }
  .contacts__icon { width: 13px; height: 13px; fill: var(--accent); flex: none; }
  .address {
    position: absolute; left: 0; right: 0; bottom: 36px;
    text-align: center; color: var(--ink); font-size: 15px;
  }
</style>
</head>
<body>
<main class="canvas">

  <section class="card card--back" aria-label="Card back">
    <div class="card__texture" role="img" aria-label="Raised texture of repeated brand marks fading from light to dark"></div>
    <div class="brand">
      <span class="brand__dot"></span>
      <span class="brand__name">Quarrow Signal Instruments</span>
    </div>
  </section>

  <section class="card card--front" aria-label="Card front">
    <div class="card__glow" role="img" aria-label="Large faint brand mark in the background"></div>

    <div class="identity">
      <p class="identity__name">Marlene</p>
      <p class="identity__role">Director</p>
    </div>
    <div class="divider"></div>

    <ul class="contacts">
      <li class="contacts__item">
        <svg class="contacts__icon" viewBox="0 0 16 16"><path d="M3 1l3 3-1.5 2a9 9 0 0 0 5.5 5.5L12 10l3 3-2 2C7 15 1 9 1 3z"/></svg>
        +001 555 210 4837
      </li>
      <li class="contacts__item">
        <svg class="contacts__icon" viewBox="0 0 16 16"><rect x="1" y="6" width="14" height="9" rx="1"/><rect x="4" y="1" width="8" height="5"/></svg>
        +001 555 210 4902
      </li>
      <li class="contacts__item">
        <svg class="contacts__icon" viewBox="0 0 16 16"><circle cx="8" cy="8" r="7"/></svg>
        www.quarrowsignal.com
      </li>
      <li class="contacts__item">
        <svg class="contacts__icon" viewBox="0 0 16 16"><path d="M1 4h14v9H1z M1 4l7 5 7-5" stroke="#3c3c3e" stroke-width="1"/></svg>
        info@quarrowsignal.com
      </li>
    </ul>

    <p class="address">118 Fenwick Park Road &bull; Alderton, CO 80999</p>
  </section>

</main>
</body>
</html>
```